Business cards to launch an education platform

Hi,
I am looking at having new business cards designed.
I am a startup, developing a web platform for schools and university, the education world. It's an online assessment system.
I would like a card that looks classy, and that is using the colors and the font of my logo.

I have attached:
1) my logo
2) A business card that I have designed quickly so you can have all the information required in the card, but I really don't like it.
3) The font that I am using (Lato Regular) to design my web platform
4) Some screenshots of my web platform so you can have a look at the style that I have.

Target Market(s)

Major market: Education system: Schools and university
Minor markets: Business in general

Industry/Entity Type

Business

Contact Information for Business Card

Clara Fenwick
Director

M: 0437 518 902
E: clara.fenwick@amberLoomSystems.com.au

Requirements
Must have
• The colors of my logo

```html
<!DOCTYPE html>
<html lang="en">
<head>
<meta charset="utf-8">
<title>Amber Loom Systems – Business Cards</title>
<link rel="stylesheet" href="https://fonts.googleapis.com/css2?family=Roboto+Condensed:wght@400;700&family=Open+Sans:ital,wght@1,400&display=swap">
<style>
  :root {
    --backdrop: #3b3431;
    --card: #1b1b1d;
    --card-edge: #111113;
    --brand-blue: #1e9fd8;
    --brand-deep: #1b6fa8;
    --text-light: #f1f3f5;
    --text-muted: #8a8f96;
    --divider: #5b6068;
  }
  * { box-sizing: border-box; margin: 0; padding: 0; }
  html, body {
    width: 1200px; height: 814px; overflow: hidden;
    background: var(--backdrop);
  }
  .stage {
    position: relative; width: 1200px; height: 814px;
    display: flex; align-items: center; justify-content: center; gap: 60px;
  }
  .card {
    position: relative; width: 520px; height: 316px;
    background: var(--card);
    border: 1px solid var(--card-edge);
    box-shadow: 0 14px 30px rgba(0,0,0,0.45);
  }

  /* Brand lockup */
  .brand { display: flex; align-items: center; gap: 14px; }
  .brand-square {
    width: 46px; height: 46px; background: var(--brand-deep); flex: none;
  }
  .brand-name {
    font-family: "Roboto Condensed", sans-serif; font-weight: 400;
    color: var(--brand-blue); letter-spacing: 2px; line-height: 1.1;
    text-transform: uppercase;
  }

  /* Front */
  .card-front .brand { position: absolute; left: 110px; top: 108px; }
  .card-front .brand-name { font-size: 30px; }
  .card-front .website {
    position: absolute; left: 110px; top: 196px;
    font-family: "Open Sans", sans-serif; font-style: italic;
    font-size: 15px; color: var(--text-muted);
  }

  /* Back */
  .card-back .brand {
    position: absolute; left: 30px; top: 120px;
    flex-direction: column; align-items: flex-start; gap: 10px;
  }
  .card-back .brand-square { width: 40px; height: 40px; }
  .card-back .brand-name { font-size: 20px; letter-spacing: 1.5px; }
  .card-back .divider {
    position: absolute; left: 218px; top: 78px; width: 1px; height: 160px;
    background: linear-gradient(to bottom, transparent, var(--divider) 20%, var(--divider) 80%, transparent);
  }
  .contact { position: absolute; left: 240px; top: 88px; font-family: "Roboto Condensed", sans-serif; }
  .contact-name { font-size: 28px; font-weight: 700; color: var(--brand-blue); line-height: 1; }
  .contact-role { font-size: 17px; font-weight: 700; color: var(--text-light); margin-top: 6px; }
  .contact-list { list-style: none; margin-top: 24px; }
  .contact-list li {
    display: flex; align-items: center; gap: 8px;
    font-size: 14.5px; color: var(--text-light); margin-bottom: 6px; white-space: nowrap;
  }
  .contact-list svg { width: 13px; height: 13px; flex: none; }
</style>
</head>
<body>
<main class="stage">
  <section class="card card-front" aria-label="Business card front">
    <div class="brand">
      <span class="brand-square"></span>
      <span class="brand-name">Amber Loom<br>Systems</span>
    </div>
    <p class="website">www.amberLoomSystems.com.au</p>
  </section>

  <section class="card card-back" aria-label="Business card back">
    <div class="brand">
      <span class="brand-square"></span>
      <span class="brand-name">Amber Loom<br>Systems</span>
    </div>
    <span class="divider"></span>
    <div class="contact">
      <p class="contact-name">Clara Fenwick</p>
      <p class="contact-role">Director</p>
      <ul class="contact-list">
        <li>
          <svg viewBox="0 0 16 16" aria-hidden="true"><rect x="4" y="1" width="8" height="14" rx="1.5" fill="none" stroke="#1e9fd8" stroke-width="1.6"/><circle cx="8" cy="12.5" r="0.9" fill="#1e9fd8"/></svg>
          0437 518 902
        </li>
        <li>
          <svg viewBox="0 0 16 16" aria-hidden="true"><rect x="1" y="3" width="14" height="10" fill="#1e9fd8"/><path d="M1 3 L8 9 L15 3" fill="none" stroke="#1b1b1d" stroke-width="1.4"/></svg>
          clara.fenwick@amberLoomSystems.com.au
        </li>
        <li>
          <svg viewBox="0 0 16 16" aria-hidden="true"><circle cx="8" cy="8" r="6.5" fill="none" stroke="#1e9fd8" stroke-width="1.5"/><ellipse cx="8" cy="8" rx="2.8" ry="6.5" fill="none" stroke="#1e9fd8" stroke-width="1.2"/><line x1="1.5" y1="8" x2="14.5" y2="8" stroke="#1e9fd8" stroke-width="1.2"/></svg>
          www.amberLoomSystems.com.au
        </li>
      </ul>
    </div>
  </section>
</main>
</body>
</html>
```